Re-design Quince zFone's new qOS7 design!

We would like designers to re-design Quince zFone's new home screen graphics - that is, the new qOS7 design announced last week at the Global Builders Summit (GBSM) 2013!

Designers are invited to take a crack at redesigning Quince’s qOS7 icons on the homepage screen. Please submit funny / satirical designs as well as your best 'serious' designs.

As background, when Quince announced qOS7 last week at GBSM 2013, designers around the world were at the edge of their seats. We were all eagerly waiting for a new, fresh, creative take on the older qOS.

While we were blown away by the features and capabilities of the new version, the icons were a big disappointment.

We’d like you to create a funny / satirical new icon designs (For example - see the funny designs that have been uploaded onto blogrix that take the fluro / gradient style too the extreme: http://marcotewrebuildsitems.blogrix.example/). Designers are free to create what you wish the icons could look like, or you can produce work you think Quince would consider using.

All you need to do is redesign the homepage screen!

Your design may include new designs for the following icons on the homepage ...
- Settings
- Mail
- Voyager
- qTracks
- Phone
- Message

qOS7 website: http://www.quince.example/qos/qos7/
Official Quince launch video: http://www.vidtube.example/watch?v=K7TPmaL3qen

Grab images here for qOS7 here: http://www.quince.example/pr/products/qos/qos.html

The Fine Print: this contest is not posted or endorsed by Quince. The winners of the contest may not be used by Quince.

Reason: Hi designers, we're extending the deadline to give more designers a chance to submit.

```html
<!DOCTYPE html>
<html lang="en">
<head>
<meta charset="utf-8">
<title>qOS7 Home Screen Redesign</title>
<link rel="stylesheet" href="https://fonts.googleapis.com/css2?family=Roboto:wght@400;500&display=swap">
<style>
  :root {
    --stage: #003049;
    --wall-left: #8ce766;
    --wall-right: #27ecc9;
    --band-top: rgba(18, 170, 160, 0.45);
    --band-dock: rgba(22, 120, 110, 0.42);
    --ink-dark: #0c3f4c;
    --label: #ffffff;
    --battery-fill-a: #f2c230;
    --battery-fill-b: #7ed957;
    --phone-a: #8fe05a;
    --phone-b: #3cc49a;
    --mail-a: #d4143f;
    --mail-b: #9a1030;
    --mail-paper: #c8f3ee;
    --msg-bg: #062c47;
    --msg-a: #9cf06a;
    --msg-b: #2fe5c4;
    --msg-c: #ff3d5a;
    --msg-d: #ffc63a;
    --settings-a: #b6f000;
    --settings-b: #22e8d2;
  }
  * { margin: 0; padding: 0; box-sizing: border-box; }
  html, body {
    width: 1200px;
    height: 904px;
    overflow: hidden;
    background: var(--stage);
    font-family: "Roboto", Arial, sans-serif;
  }
  .screen {
    position: absolute;
    left: 361px;
    top: 30px;
    width: 476px;
    height: 843px;
    overflow: hidden;
    background: linear-gradient(90deg, var(--wall-left), var(--wall-right));
  }
  .wallpaper {
    position: absolute;
    left: 0; top: 0;
    width: 476px; height: 843px;
  }
  .screen-bands {
    position: absolute;
    left: 0; top: 0;
  }
  .status-bar {
    position: absolute;
    left: 0; top: 0;
    width: 476px; height: 34px;
    color: var(--ink-dark);
    font-size: 15px;
  }
  .status-signal { position: absolute; left: 7px; top: 9px; }
  .status-time {
    position: absolute;
    left: 0; right: 0; top: 8px;
    text-align: center;
    letter-spacing: 0.3px;
  }
  .status-battery {
    position: absolute;
    right: 6px; top: 8px;
    display: flex; align-items: center; gap: 5px;
  }
  .dock {
    position: absolute;
    left: 0; top: 735px;
    width: 476px;
    display: flex;
  }
  .app {
    position: absolute;
    width: 76px;
    text-align: center;
  }
  .app-phone { left: 40px; }
  .app-mail { left: 148px; }
  .app-messages { left: 256px; }
  .app-settings { left: 366px; }
  .app-icon {
    display: block;
    width: 76px; height: 76px;
    border-radius: 17px;
    overflow: hidden;
    box-shadow: 0 2px 6px rgba(0, 60, 60, 0.25);
  }
  .app-icon svg { display: block; }
  .icon-phone { background: linear-gradient(150deg, var(--phone-a), var(--phone-b)); }
  .icon-mail { background: linear-gradient(180deg, var(--mail-a), var(--mail-b)); }
  .icon-messages { background: var(--msg-bg); }
  .icon-settings { background: linear-gradient(160deg, var(--settings-a), var(--settings-b)); }
  .app-label {
    display: block;
    width: 110px;
    margin-left: -17px;
    margin-top: 4px;
    color: var(--label);
    font-size: 15px;
    letter-spacing: 0.2px;
  }
</style>
</head>
<body>
<main class="screen">
  <div class="wallpaper" role="img" aria-label="Wallpaper with faint translucent geometric X decorations"></div>

  <svg class="screen-bands" width="476" height="843" viewBox="0 0 476 843" aria-hidden="true">
    <path d="M0 0 H476 V42 Q238 22 0 42 Z" fill="var(--band-top)"/>
    <path d="M0 706 Q238 686 476 706 V843 H0 Z" fill="var(--band-dock)"/>
  </svg>

  <header class="status-bar">
    <svg class="status-signal" width="76" height="20" viewBox="0 0 76 20" aria-label="Signal and Wi-Fi">
      <g fill="var(--ink-dark)">
        <circle cx="4" cy="11" r="3.6"/>
        <circle cx="12" cy="14" r="3.6"/>
        <circle cx="20" cy="11" r="3.6"/>
        <circle cx="28" cy="14" r="3.6"/>
        <circle cx="36" cy="10" r="3.6"/>
      </g>
      <g fill="none" stroke="var(--ink-dark)" stroke-width="2.6" stroke-linecap="round">
        <path d="M48 7 Q60 -3 72 7"/>
        <path d="M52 11 Q60 4 68 11"/>
        <path d="M56 15 Q60 12 64 15"/>
      </g>
      <circle cx="60" cy="18" r="1.8" fill="var(--ink-dark)"/>
    </svg>
    <div class="status-time">9:41 AM</div>
    <div class="status-battery">
      <span>100%</span>
      <svg width="42" height="14" viewBox="0 0 42 14" aria-hidden="true">
        <defs>
          <linearGradient id="batteryFill" x1="0" x2="1">
            <stop offset="0" stop-color="var(--battery-fill-a)"/>
            <stop offset="1" stop-color="var(--battery-fill-b)"/>
          </linearGradient>
        </defs>
        <rect x="1" y="1" width="37" height="12" fill="none" stroke="var(--ink-dark)" stroke-width="1.5"/>
        <rect x="3" y="3" width="33" height="8" fill="url(#batteryFill)"/>
        <rect x="39" y="4.5" width="2.5" height="5" fill="var(--ink-dark)"/>
      </svg>
    </div>
  </header>

  <nav class="dock" aria-label="Dock">
    <div class="app app-phone">
      <span class="app-icon icon-phone">
        <svg width="76" height="76" viewBox="0 0 76 76" aria-hidden="true">
          <path d="M24 15 Q17 17 17 26 Q20 45 36 57 Q46 64 54 60 L58 54 L48 46 L42 51 Q32 44 27 33 L32 27 L26 15 Z" fill="#e24a8a" transform="translate(-3 2)"/>
          <path d="M24 15 Q17 17 17 26 Q20 45 36 57 Q46 64 54 60 L58 54 L48 46 L42 51 Q32 44 27 33 L32 27 L26 15 Z" fill="#ffffff"/>
        </svg>
      </span>
      <span class="app-label">Phone</span>
    </div>
    <div class="app app-mail">
      <span class="app-icon icon-mail">
        <svg width="76" height="76" viewBox="0 0 76 76" aria-hidden="true">
          <rect x="10" y="20" width="56" height="40" fill="var(--mail-paper)"/>
          <path d="M10 60 L38 38 L66 60" fill="none" stroke="var(--mail-b)" stroke-width="2.5"/>
          <path d="M10 20 L38 44 L66 20 Z" fill="var(--mail-a)"/>
        </svg>
      </span>
      <span class="app-label">Mail</span>
    </div>
    <div class="app app-messages">
      <span class="app-icon icon-messages">
        <svg width="76" height="76" viewBox="0 0 76 76" aria-hidden="true">
          <defs>
            <linearGradient id="bubbleBig" x1="0" x2="1">
              <stop offset="0" stop-color="var(--msg-a)"/>
              <stop offset="1" stop-color="var(--msg-b)"/>
            </linearGradient>
            <linearGradient id="bubbleSmall" x1="0" y1="1" x2="1" y2="0">
              <stop offset="0" stop-color="var(--msg-c)"/>
              <stop offset="1" stop-color="var(--msg-d)"/>
            </linearGradient>
          </defs>
          <path d="M20 12 H58 V38 H24 V34 L12 38 L20 32 Z" fill="url(#bubbleBig)"/>
          <path d="M36 46 H54 L62 60 H36 Z" fill="url(#bubbleSmall)"/>
        </svg>
      </span>
      <span class="app-label">Messages</span>
    </div>
    <div class="app app-settings">
      <span class="app-icon icon-settings" role="img" aria-label="Settings icon artwork of crossed dark navy cog shapes"></span>
      <span class="app-label">Settings</span>
    </div>
  </nav>
</main>
</body>
</html>
```